Orthobiologic, StemCell, Bone Marrow Aspirate Device Distributor

We need a wordpress fully functioning website design for an innovative ortho-biologic, Bone Marrow Aspirate Device that extracts stem cells for orthopedic regenerative medical professionals. We also offer state of the art training in there office setting with licensed medical staff, a full service support team, and software for tracking patient outcome over time. We are an innovative company that prides itself on gold standard support. We will have other offerings on our website and would like a spot for "future" products. We would like to see designs that look professional, medical, and convey support, security, science, and innovation. We prefer shades of blue and red/orange. I particularly like the following websites that also sell the same device in order of preference:regenacelltherapy.comhttps://aspire-medical.eu/marrow-cellution/https://www.matrixbiosurgical.com/#emerging-solutions-in-healthcareElite2elite.comI have attached a few pictures of the device for reference

Target Market(s)

Orthopedics, Regenerative medicine doctors, Industry representatives, Hospitals

Industry/Entity Type

Medical Equipment

Coding

Coded - Design and coding required

Colors
3176b5
33a6d7
f37022
ec1f27

Requirements
Must have
• It must be able to have videos which I can supply, email, online ordering, and sfax. I have a domain name Coralweavesolutions.com . It must have a FAQ section which you can obtain some information from https://www.tolvenclinical.com/solutions#resources
• The device is manufactured by Dulmor and this is the link to the product page http://www.dulmor.com/quintadraw
• I am currently working on a custom logo and should be able to supply that in short order. I prefer shades of blue and red.
Nice to have
• I would love to have a graphic video as seen here: please see quinta draw vs bone marrow aspirate concentrate.
• https://www.tolvenclinical.com/solutions#competition
• I would pay considerably more to have something similar if it is at all possible
Should not have
• Nothing specific

```html
<!DOCTYPE html>
<html lang="en">
<head>
<meta charset="utf-8">
<title>Coralweave Solutions</title>
<link rel="stylesheet" href="https://fonts.googleapis.com/css2?family=Josefin+Sans:wght@300;700&family=Roboto:wght@400;500;700&display=swap">
<style>
:root{
  --blue:#2a5ea9;
  --blue-dark:#0f2246;
  --orange:#f15a24;
  --red:#ec1f27;
  --ink:#2b2b2b;
  --muted:#6d6d6d;
  --card:#f3f2f1;
  --line:#e2e2e2;
  --white:#fff;
}
*{box-sizing:border-box;margin:0;padding:0}
html,body{width:1200px;height:4141px;overflow:hidden}
body{position:relative;font-family:"Roboto",Arial,sans-serif;color:var(--ink);background:var(--white)}
.abs{position:absolute}
.display{font-family:"Josefin Sans",sans-serif}
.display b{font-weight:700}
.display span{font-weight:300}
.rule{position:absolute;height:3px;width:112px;background:var(--orange)}

/* header */
.site-header{position:absolute;top:0;left:0;width:1200px;height:100px;border-top:3px solid var(--orange);background:var(--white)}
.brand{position:absolute;left:145px;top:32px;font:700 34px "Josefin Sans",sans-serif;color:var(--blue)}
.nav{position:absolute;left:575px;top:42px;display:flex;gap:30px;font:500 14px "Roboto",sans-serif;color:#222}
.nav svg{margin-top:-1px}

/* hero */
.hero{position:absolute;top:100px;left:0;width:1200px;height:522px;
  background:radial-gradient(ellipse 260px 300px at 600px 280px,#e8792c 0%,#b8462a 35%,rgba(40,70,190,0) 75%),linear-gradient(90deg,#06123a 0%,#1e3fb8 35%,#2446c4 65%,#08133d 100%)}
.hero-title{position:absolute;top:198px;width:1200px;text-align:center;font:700 78px "Josefin Sans",sans-serif;color:var(--white)}
.hero-sub{position:absolute;top:298px;width:1200px;text-align:center;font:700 17px "Roboto",sans-serif;color:var(--white)}

/* welcome */
.welcome{position:absolute;top:622px;left:0;width:1200px;height:338px;
  background:radial-gradient(ellipse 300px 200px at 1000px 130px,#f6d2cc 0%,rgba(255,255,255,0) 70%),radial-gradient(ellipse 260px 220px at 80px 170px,#f4e3dc 0%,rgba(255,255,255,0) 70%),#fdf9f7}
.welcome h2{position:absolute;top:58px;width:1200px;text-align:center;color:var(--blue);line-height:1.1}
.welcome h2 b{display:block;font-size:42px}
.welcome h2 span{display:block;font-size:38px}
.welcome p{position:absolute;top:190px;left:200px;width:800px;text-align:center;font-size:12.5px;line-height:29px;color:#555}

/* why */
.why{position:absolute;top:960px;left:0;width:1200px;height:448px;background:linear-gradient(180deg,#dde1e6,#c9d0d8)}
.why-photo{position:absolute;right:0;top:0;width:600px;height:448px;background:linear-gradient(90deg,rgba(210,216,222,0) 0%,#b9c4cf 30%,#e4e8ec 60%,#f0f2f5 100%)}
.why h2{position:absolute;left:143px;top:95px;font-size:40px;color:var(--blue)}
.why h2 span{color:var(--orange)}
.why p{position:absolute;left:143px;top:178px;width:470px;font-size:12.5px;line-height:30px;color:#555}

/* values */
.values h2,.advantages h2{position:absolute;top:1472px;font-size:40px;color:var(--blue)}
.accordion-item{position:absolute;left:143px;width:378px;height:50px;background:var(--white);box-shadow:0 2px 6px rgba(0,0,0,.18);font:500 16px "Roboto",sans-serif;padding:15px 24px;color:#222}
.accordion-item i{position:absolute;right:8px;top:9px;width:32px;height:32px;background:var(--orange);color:#fff;font:400 22px/30px "Roboto",sans-serif;text-align:center;font-style:normal}
.accordion-gap{position:absolute;left:143px;width:378px;height:12px;background:#dcdcdc}
.adv{position:absolute;left:615px;width:450px}
.adv-icon{position:absolute;left:0;top:0;width:66px;height:66px;border:1px solid #ddd;border-radius:50%;display:flex;align-items:center;justify-content:center}
.adv h3{position:absolute;left:85px;top:-6px;font:500 19px "Roboto",sans-serif;color:#222;white-space:nowrap}
.adv p{position:absolute;left:86px;top:24px;width:370px;font-size:12.5px;line-height:21px;color:#777}

/* faq */
.faq{position:absolute;top:1901px;left:0;width:1200px;height:717px;background:radial-gradient(ellipse 280px 380px at 950px 380px,#6c2230 0%,rgba(20,30,70,0) 75%),radial-gradient(ellipse 300px 380px at 230px 360px,#1f5aa0 0%,rgba(20,30,70,0) 75%),linear-gradient(180deg,#0f1d38,#12244a 50%,#0d1a33)}
.faq h2{position:absolute;top:90px;width:1200px;text-align:center;font-size:40px;color:var(--white);letter-spacing:1px}
.faq-q{position:absolute;left:251px;width:697px;height:54px;border-radius:27px;background:var(--white);font:500 14.5px/54px "Roboto",sans-serif;padding-left:32px;color:#111;white-space:nowrap}
.faq-q i{position:absolute;right:8px;top:9px;width:36px;height:36px;border-radius:50%;background:var(--orange);color:#fff;font:700 20px/35px "Roboto",sans-serif;text-align:center;font-style:normal}
.faq-a{position:absolute;left:283px;top:2190px;width:640px;font-size:12.5px;line-height:29px;color:#e4e8ef}

/* events */
.events h2{position:absolute;top:2690px;width:1200px;text-align:center;font-size:42px;color:var(--blue)}
.event{position:absolute;width:294px;height:272px;background:var(--card);border:1px solid #e6e4e2;text-align:center}
.event svg{margin-top:34px}
.event h3{font:400 20px "Roboto",sans-serif;color:#222;margin-top:14px}
.event .date{font-size:13px;color:var(--orange);margin-top:10px}
.event p{font-size:12.5px;line-height:21px;color:#777;margin:10px auto 0;width:240px}
.event a{display:block;margin-top:16px;font:700 12px "Roboto",sans-serif;color:var(--blue);text-decoration:none}
.event.featured{background:var(--blue);border-color:var(--blue)}
.event.featured h3,.event.featured p,.event.featured a{color:#fff}

/* tiles */
.tile{position:absolute;top:3434px;height:378px;display:flex;align-items:flex-end;justify-content:center;font:700 29px "Roboto",sans-serif;color:#fff}
.tile-products{left:0;width:397px;background:radial-gradient(ellipse 180px 200px at 180px 190px,#3f7fbf,#123058 70%,#0b1e3a)}
.tile-providers{left:397px;width:400px;background:linear-gradient(135deg,#f27a3c,#e8682b 50%,#f08a4d)}
.tile-distributors{left:797px;width:403px;background:linear-gradient(180deg,#c8d0da,#8b99ad 60%,#4f5f78)}
.tile span{margin-bottom:48px}
.tile-providers .inner{position:absolute;top:140px;width:400px;text-align:center}
.tile-providers .inner hr{width:96px;border:0;border-top:2px solid #fff;margin:18px auto 24px}
.tile-providers .inner a{font:400 14px "Roboto",sans-serif;color:#fff;text-decoration:underline}

/* footer */
.footer-brand{position:absolute;left:146px;top:3873px;font:700 34px "Josefin Sans",sans-serif;color:var(--blue)}
.footer-about{position:absolute;left:146px;top:3928px;width:350px;font-size:12px;line-height:20px;color:#444}
.socials{position:absolute;left:146px;top:3993px;display:flex;gap:8px}
.socials i{width:30px;height:30px;border:1.5px solid var(--blue);border-radius:50%;display:block}
.footer h4{position:absolute;top:3873px;font:700 15px "Roboto",sans-serif;color:#222}
.news-text{position:absolute;left:554px;top:3906px;width:240px;font-size:11.5px;line-height:17px;color:#555}
.news-input{position:absolute;left:554px;top:3950px;width:229px;height:38px;border:1px solid #ccc;font-size:11px;color:#555;padding:12px 12px}
.news-btn{position:absolute;left:554px;top:4001px;width:115px;height:27px;background:var(--orange);color:#fff;font:500 12px/27px "Roboto",sans-serif;text-align:center}
.contact-item{position:absolute;left:850px;display:flex;gap:10px;font-size:12px;line-height:20px;color:#444;width:210px}
.live-chat{position:absolute;left:1168px;top:3881px;width:32px;height:152px;background:var(--red);color:#fff;font:700 14px "Roboto",sans-serif;writing-mode:vertical-rl;transform:rotate(180deg);text-align:center;line-height:32px}
.copyright{position:absolute;top:4082px;left:0;width:1200px;height:59px;border-top:1px solid var(--line);text-align:center;font-size:11px;line-height:59px;color:#444}
</style>
</head>
<body>

<header class="site-header">
  <div class="brand">Coralweave Solutions</div>
  <nav class="nav">
    <span>HOME</span><span>ABOUT US</span><span>SERVICES</span><span>BLOG</span><span>CONTACT US</span>
    <svg width="16" height="16" viewBox="0 0 16 16"><circle cx="6.5" cy="6.5" r="5" fill="none" stroke="#222" stroke-width="2"/><path d="M10.5 10.5 15 15" stroke="#222" stroke-width="2.2"/></svg>
  </nav>
</header>

<section class="hero" role="img" aria-label="X-ray style illustration of a glowing human spine and pelvis"></section>
<h1 class="hero-title">Coralweave Solutions</h1>
<p class="hero-sub">Sed ut perspiciatis unde omnis iste natt voluptatem accusantium</p>

<section class="welcome" role="img" aria-label="Soft microscopic cell imagery in pale pink tones">
  <h2 class="display"><b>Welcome to</b><span>Coralweave Solutions</span></h2>
  <div class="rule" style="top:162px;left:544px"></div>
  <p>Sed ut perspiciatis unde omnis iste natus error sit voluptatem accusantium doloremque laudantium, totam rem aperiam, eaque ipsa quae ab illo inventore veritatis et quasi architecto beatae vitae dicta sunt explicabo. Nemo enim ipsam voluptatem quia voluptas sit aspernatur aut odit aut fugit, sed quia consequuntur magni dolores eos qui ratione voluptatem sequi nesciunt.</p>
</section>

<section class="why">
  <div class="why-photo" role="img" aria-label="Photo of a smiling doctor with a stethoscope, colleagues working in the background"></div>
  <svg class="abs" style="left:897px;top:154px" width="60" height="60" viewBox="0 0 60 60"><circle cx="30" cy="30" r="27" fill="rgba(0,0,0,.25)" stroke="#fff" stroke-width="3"/><path d="M24 18 42 30 24 42Z" fill="#fff"/></svg>
  <h2 class="display"><b>Why</b> <span>Us?</span></h2>
  <div class="rule" style="top:148px;left:143px"></div>
  <p>Sed ut perspiciatis unde omnis iste natus error sit voluptatem accusantium doloremque laudantium, totam rem aperiam, eaque ipsa quae ab illo inventore veritatis et quasi architecto beatae vitae dicta sunt explicabo. Nemo enim ipsam voluptatem quia voluptas sit aspernatur aut odit aut fugit, sed quia consequuntur magni dolores eos qui ratione voluptatem sequi nesciuneque porro quisquam est, qui dolorem ipsum quia dolor sit ametconsectetur</p>
</section>

<section class="values">
  <h2 class="display" style="left:143px"><b>Our</b> <span>Values</span></h2>
  <div class="rule" style="top:1525px;left:143px"></div>
  <div class="accordion-item" style="top:1571px">Our Mission<i>+</i></div>
  <div class="accordion-gap" style="top:1621px"></div>
  <div class="accordion-item" style="top:1635px">Our Vision<i>+</i></div>
  <div class="accordion-gap" style="top:1685px"></div>
  <div class="accordion-item" style="top:1699px">Our Commitment<i>+</i></div>
</section>

<section class="advantages">
  <h2 class="display" style="left:615px"><b>Our</b> <span>Advantages</span></h2>
  <div class="rule" style="top:1525px;left:615px"></div>
  <div class="adv" style="top:1574px">
    <div class="adv-icon"><svg width="26" height="30" viewBox="0 0 26 30"><path d="M13 3a8 8 0 0 0-5 14v4h10v-4a8 8 0 0 0-5-14Z" fill="none" stroke="#f15a24" stroke-width="2.4"/><path d="M9 25h8M10 28h6" stroke="#f15a24" stroke-width="2.4"/></svg></div>
    <h3>Innovative</h3>
    <p>Sed ut perspiciatis unde omnis iste natus error sit voluptatem accusantium doloremque laudantium,</p>
  </div>
  <div class="adv" style="top:1670px">
    <div class="adv-icon"><svg width="28" height="28" viewBox="0 0 28 28"><path d="M10 3h8M11 3v8L4 24h20l-7-13V3" fill="none" stroke="#f15a24" stroke-width="2.2"/><path d="M7 19h14l3 5H4Z" fill="#f15a24"/></svg></div>
    <h3>Science-Based</h3>
    <p>Sed ut perspiciatis unde omnis iste natus error sit voluptatem accusantium doloremque laudantium,</p>
  </div>
  <div class="adv" style="top:1766px">
    <div class="adv-icon"><svg width="28" height="30" viewBox="0 0 28 30"><path d="M6 3v8a6 6 0 0 0 12 0V3M12 17v5a5 5 0 0 0 10 0v-4" fill="none" stroke="#f15a24" stroke-width="2.2"/><circle cx="22" cy="15" r="3" fill="none" stroke="#f15a24" stroke-width="2.2"/></svg></div>
    <h3>Ethically Driven</h3>
    <p>Sed ut perspiciatis unde omnis iste natus error sit voluptatem accusantium doloremque laudantium,</p>
  </div>
</section>

<section class="faq" role="img" aria-label="Dark X-ray imagery of a pelvis with a hip joint highlighted in red">
  <h2 class="display"><b>FREQUENTLY</b> <span>ASKED QUESTIONS</span></h2>
  <div class="rule" style="top:150px;left:544px"></div>
</section>
<div class="faq-q" style="top:2118px">WHAT IS THE PURPOSE OF CENTRIFUGATION PROTOCOLS FOR MARROW?<i>–</i></div>
<p class="faq-a">Sed ut perspiciatis unde omnis iste natus error sit voluptatem accusantium doloremque laudantium, totam rem aperiam, eaque ipsa quae ab illo inventore veritatis et quasi architecto beatae vitae dicta sunt explicabo. Nemo enim ipsam voluptatem quia voluptas sit aspernatur aut odit aut fugit, sed quia consequuntur magni dolores eos qui ratione voluptatem sequi nesciunt. Neque porro quisquam est, qui dolorem</p>
<div class="faq-q" style="top:2322px">DOES THE NUMBER OF CD34+ CELLS IN MARROW DECLINE WITH AGE?<i>+</i></div>
<div class="faq-q" style="top:2394px">WHAT IS THE IMPORTANCE OF CD34 COMPARED TO NUCLEATED CELL COUNTS?<i>+</i></div>
<div class="faq-q" style="top:2466px">CAN THE QUINTA DRAW NEEDLE BE USED TO ASPIRATE FROM BONES..?<i>+</i></div>

<section class="events">
  <h2 class="display"><b>Upcoming</b> <span>Events</span></h2>
  <div class="rule" style="top:2744px;left:544px"></div>
</section>

<div class="event" style="left:143px;top:2810px"><svg width="34" height="34" viewBox="0 0 34 34"><rect x="2" y="6" width="30" height="26" fill="none" stroke="#f15a24" stroke-width="2.5"/><path d="M2 6h30v8H2Z" fill="#f15a24"/><path d="M10 2v8M24 2v8" stroke="#f15a24" stroke-width="2.5"/></svg><h3>Sed utperspiciatis</h3><div class="date">July 11-14, 2019</div><p>Lorem ipsum dolor sit amet consectetur adipiscing elied do eiusmod</p><a>READ MORE &nbsp;»</a></div>
<div class="event featured" style="left:454px;top:2795px"><svg width="34" height="34" viewBox="0 0 34 34"><rect x="2" y="6" width="30" height="26" fill="none" stroke="#fff" stroke-width="2.5"/><path d="M2 6h30v8H2Z" fill="#fff"/><path d="M10 2v8M24 2v8" stroke="#fff" stroke-width="2.5"/></svg><h3>Sed utperspiciatis</h3><div class="date">July 11-14, 2019</div><p>Lorem ipsum dolor sit amet consectetur adipiscing elied do eiusmod</p><a>READ MORE &nbsp;»</a></div>
<div class="event" style="left:763px;top:2810px"><svg width="34" height="34" viewBox="0 0 34 34"><rect x="2" y="6" width="30" height="26" fill="none" stroke="#f15a24" stroke-width="2.5"/><path d="M2 6h30v8H2Z" fill="#f15a24"/><path d="M10 2v8M24 2v8" stroke="#f15a24" stroke-width="2.5"/></svg><h3>Sed utperspiciatis</h3><div class="date">July 11-14, 2019</div><p>Lorem ipsum dolor sit amet consectetur adipiscing elied do eiusmod</p><a>READ MORE &nbsp;»</a></div>
<div class="event" style="left:143px;top:3096px"><svg width="34" height="34" viewBox="0 0 34 34"><rect x="2" y="6" width="30" height="26" fill="none" stroke="#f15a24" stroke-width="2.5"/><path d="M2 6h30v8H2Z" fill="#f15a24"/><path d="M10 2v8M24 2v8" stroke="#f15a24" stroke-width="2.5"/></svg><h3>Sed utperspiciatis</h3><div class="date">July 11-14, 2019</div><p>Lorem ipsum dolor sit amet consectetur adipiscing elied do eiusmod</p><a>READ MORE &nbsp;»</a></div>
<div class="event" style="left:454px;top:3080px"><svg width="34" height="34" viewBox="0 0 34 34"><rect x="2" y="6" width="30" height="26" fill="none" stroke="#f15a24" stroke-width="2.5"/><path d="M2 6h30v8H2Z" fill="#f15a24"/><path d="M10 2v8M24 2v8" stroke="#f15a24" stroke-width="2.5"/></svg><h3>Sed utperspiciatis</h3><div class="date">July 11-14, 2019</div><p>Lorem ipsum dolor sit amet consectetur adipiscing elied do eiusmod</p><a>READ MORE &nbsp;»</a></div>
<div class="event" style="left:763px;top:3096px"><svg width="34" height="34" viewBox="0 0 34 34"><rect x="2" y="6" width="30" height="26" fill="none" stroke="#f15a24" stroke-width="2.5"/><path d="M2 6h30v8H2Z" fill="#f15a24"/><path d="M10 2v8M24 2v8" stroke="#f15a24" stroke-width="2.5"/></svg><h3>Sed utperspiciatis</h3><div class="date">July 11-14, 2019</div><p>Lorem ipsum dolor sit amet consectetur adipiscing elied do eiusmod</p><a>READ MORE &nbsp;»</a></div>

<div class="tile tile-products" role="img" aria-label="X-ray of a hip with an implant highlighted"><span>PRODUCTS</span></div>
<div class="tile tile-providers" role="img" aria-label="Orange-toned photo of a hand holding a tablet">
  <div class="inner"><div>PROVIDERS</div><hr><a>View More</a></div>
</div>
<div class="tile tile-distributors" role="img" aria-label="Photo of medical staff in scrubs walking down a hospital corridor"><span>DISTRIBUTORS</span></div>

<footer class="footer">
  <div class="footer-brand">Coralweave Solutions</div>
  <p class="footer-about">Sed ut perspiciatis unde omnis iste natus error sit voluptatem accusantium doloremque laudanSed ut perspiciatis unde omnis iste natus erraising rortium,</p>
  <div class="socials"><i></i><i></i><i></i><i></i></div>

  <h4 style="left:554px">SIGN UP FOR NEWSLETTER</h4>
  <p class="news-text">Excepteur sint occaecat cupidatat non proideulpa qui officia deserunt</p>
  <div class="news-input">Enter email</div>
  <div class="news-btn">SUBSCRIPTION</div>

  <h4 style="left:850px">CONTACT US</h4>
  <div class="contact-item" style="top:3912px"><svg width="12" height="16" viewBox="0 0 12 16"><path d="M6 1a5 5 0 0 0-5 5c0 4 5 9 5 9s5-5 5-9a5 5 0 0 0-5-5Z" fill="none" stroke="#2a5ea9" stroke-width="1.6"/><circle cx="6" cy="6" r="1.8" fill="#2a5ea9"/></svg><span>12.Sed ut perspiciatis unde omnis iste natus error</span></div>
  <div class="contact-item" style="top:3960px"><svg width="12" height="14" viewBox="0 0 12 12"><path d="M2 1l2.5 0 1 3-1.5 1a7 7 0 0 0 3 3l1-1.5 3 1V10a1 1 0 0 1-1 1A10 10 0 0 1 1 2a1 1 0 0 1 1-1Z" fill="#2a5ea9"/></svg><span>Phone: &nbsp;1-800-888-8888</span></div>
  <div class="contact-item" style="top:3988px"><svg width="12" height="14" viewBox="0 0 12 10"><rect x="0.5" y="1" width="11" height="8" fill="#2a5ea9"/><path d="M1 1.5 6 5.5l5-4" fill="none" stroke="#fff" stroke-width="1"/></svg><span>info@coralweavesolutions.com</span></div>
</footer>

<div class="live-chat">LIVE CHAT</div>

<div class="copyright">©2019 Coralweave Solutions All Rights Reserved | Privacy policy &nbsp;| &nbsp;Terms and Use</div>

</body>
</html>
```